We are a doctors medical practice
I need the business card to be eye catching and memorable,
to reflect professionalism, yet also warmth and care

the numbers need to be easy to see, for the elderly

and the logo also in a location that is large enough to see and be eye catching

Back of card:
opening hours:
Mon- Fri 8.30am to 6pm
Sat 9am to 4pm

rows for appontments, date and time
Updates

HiĀ 

Modification to company name

BROOKVALE KINDRED HEALTH MEDICAL PRACTICE

Thanks
Marla

Reason: I am look for a unique design that also fulfils the design brief

I have attempted to post a .eps and .ai file of the logo

Target Market(s)

needs to appeal to the majority, mainly adults

Industry/Entity Type

Medical

Contact Information for Business Card

company name: Brookvale Kindred Health Medical Practice
Name: Dr Marla Tobrik-Vey
Qualifications: MBBS, BMedSc, FRACGP, DRCOG, Dip Paed, Dip Skin
Address: Shop 3/41-43 Corrow St, Kellsby 2871
Ph: 02 9184 3025
Fax: 02 9318 6042

Requirements
Nice to have
• I like balance
gold/ silver incorporated, as well as the other colours in the logo- but not limited to these colours
a "medical" feel
Should not have
• dark or strong colours

```html
<!DOCTYPE html>
<html lang="en">
<head>
<meta charset="utf-8">
<title>Brookvale Kindred Health Medical Practice – Business Card</title>
<link rel="stylesheet" href="https://fonts.googleapis.com/css2?family=Open+Sans:wght@400;600;700&family=Marcellus&display=swap">
<style>
  :root {
    --page: #ecebe6;
    --olive: #b4ac08;
    --green: #22b14c;
    --navy: #1d3a6b;
    --yellow: #fff200;
    --white: #ffffff;
    --paper-light: #fbfbfb;
    --paper-grey: #d9d9d9;
    --ink: #222222;
    --ring: #9fd3ec;
  }
  * { box-sizing: border-box; margin: 0; padding: 0; }
  html, body { width: 1200px; height: 900px; overflow: hidden; }
  body {
    background: var(--page);
    font-family: "Open Sans", Arial, sans-serif;
    position: relative;
  }
  .card {
    position: absolute;
    left: 260px;
    width: 680px;
    height: 379px;
    overflow: hidden;
    box-shadow: 0 6px 18px rgba(0,0,0,0.18);
  }

  /* ---------- back: appointments ---------- */
  .card-back { top: 48px; background: linear-gradient(180deg, var(--paper-light), var(--paper-grey)); }
  .hours-band {
    height: 92px;
    background: var(--olive);
    color: var(--white);
    display: flex;
    align-items: center;
    padding-left: 30px;
    font-weight: 700;
  }
  .hours-label { font-size: 23px; letter-spacing: 1px; margin-right: 20px; white-space: nowrap; }
  .hours-times { font-size: 21px; line-height: 1.25; white-space: nowrap; }
  .hours-times span { display: block; }
  .hours-times span + span { padding-left: 22px; }
  .appointments {
    position: relative;
    padding: 16px 30px 0 30px;
  }
  .appointments-head {
    display: flex;
    justify-content: space-between;
    font-size: 15px;
    font-weight: 700;
    color: var(--ink);
    margin-bottom: 4px;
  }
  .appointment-row {
    height: 28px;
    border-bottom: 2px dotted #333;
  }
  .faint-ring {
    position: absolute;
    left: 250px; top: 110px;
    width: 240px; height: 240px;
    border-radius: 50%;
    border: 10px solid var(--ring);
    opacity: 0.3;
  }

  /* ---------- front: contact ---------- */
  .card-front { top: 473px; background: var(--olive); }
  .name-band {
    height: 98px;
    background: var(--green);
    display: flex;
    justify-content: flex-end;
    padding: 12px 34px 0 0;
  }
  .name-block { text-align: left; }
  .doctor-name {
    color: var(--yellow);
    font-size: 26px;
    font-weight: 700;
    letter-spacing: 0.5px;
    white-space: nowrap;
  }
  .qualifications {
    color: var(--white);
    font-size: 15px;
    font-weight: 600;
    line-height: 1.3;
    margin-top: 2px;
    padding-left: 12px;
    white-space: nowrap;
  }
  .practice-band {
    height: 104px;
    background: var(--white);
    display: flex;
    align-items: center;
    padding-left: 24px;
    gap: 14px;
  }
  .practice-dot {
    width: 48px; height: 48px;
    border-radius: 50%;
    background: var(--green);
    flex: none;
  }
  .practice-name {
    font-family: "Marcellus", Georgia, serif;
    color: var(--navy);
    font-size: 19px;
    font-weight: 400;
    letter-spacing: 0.3px;
    white-space: nowrap;
  }
  .contact {
    padding: 26px 0 0 34px;
    color: var(--white);
    font-size: 22px;
    font-weight: 700;
    line-height: 1.35;
  }
  .contact-row { display: flex; white-space: nowrap; }
  .contact-label { width: 112px; }
  .contact-colon { width: 26px; }
</style>
</head>
<body>

<section class="card card-back" aria-label="Appointment card, back">
  <div class="faint-ring"></div>
  <header class="hours-band">
    <span class="hours-label">OPENING HOURS:</span>
    <p class="hours-times"><span>Mon- Fri 8.30am to 6pm</span><span>Sat 9am to 4pm</span></p>
  </header>
  <div class="appointments">
    <div class="appointments-head"><span>Appontments</span><span>Date &amp; Time</span></div>
    <div class="appointment-row"></div>
    <div class="appointment-row"></div>
    <div class="appointment-row"></div>
    <div class="appointment-row"></div>
    <div class="appointment-row"></div>
    <div class="appointment-row"></div>
    <div class="appointment-row"></div>
    <div class="appointment-row"></div>
  </div>
</section>

<section class="card card-front" aria-label="Business card, front">
  <header class="name-band">
    <div class="name-block">
      <h1 class="doctor-name">Dr Marla Tobrik-Vey</h1>
      <p class="qualifications">MBBS, BMedSc, FRACGP,<br>DRCOG, Dip Paed, Dip Skin</p>
    </div>
  </header>
  <div class="practice-band">
    <span class="practice-dot"></span>
    <h2 class="practice-name">BROOKVALE KINDRED HEALTH MEDICAL PRACTICE</h2>
  </div>
  <div class="contact">
    <p class="contact-row"><span class="contact-label">Tel</span><span class="contact-colon">:</span><span>02 9184 3025</span></p>
    <p class="contact-row"><span class="contact-label">Fax</span><span class="contact-colon">:</span><span>02 9318 6042</span></p>
    <p class="contact-row"><span class="contact-label">Address</span><span class="contact-colon">:</span><span>Shop 3/41-43 Corrow St, Kellsby 2871</span></p>
  </div>
</section>

</body>
</html>
```